Business Card - connecting 2 souls and beggining the journey of self discovery

Logo on the front
with tag line

On the back list of services and contact details

Seminars
workshops
Coaching
podcasts

Darren Whitlow
Health & Wellbeing Life Coach
0491 372 615
darren@brightcoreliving.example
brightcoreliving.example

Industry/Entity Type

Life Coaching

Contact Information for Business Card

I like the use of colour from the logo to be used. I'm not a fan of white.

Requirements
Must have
• My tagline: The journey home starts with you
Nice to have
• Use of colour that is in the mind body soul logo

```html
<!DOCTYPE html>
<html lang="en">
<head>
<meta charset="utf-8">
<title>Bright Core Living – Business Card</title>
<link rel="stylesheet" href="https://fonts.googleapis.com/css2?family=Roboto:wght@400&family=Montserrat:wght@500&display=swap">
<style>
  :root {
    --backdrop: #262626;
    --card: #fcefe6;
    --ink: #4a4444;
    --ink-soft: #756d6d;
    --accent: #f2a15a;
    --violet: #9b5fb0;
    --rose: #ef7a7f;
    --sun: #f4c24a;
    --leaf: #86c66a;
    --teal: #2fb3a3;
  }
  html, body {
    margin: 0;
    padding: 0;
    width: 1200px;
    height: 1096px;
    overflow: hidden;
    background: var(--backdrop);
  }
  .canvas {
    position: relative;
    width: 1200px;
    height: 1096px;
  }
  .card {
    position: absolute;
    width: 550px;
    height: 317px;
    background: var(--card);
    box-sizing: border-box;
    overflow: hidden;
  }
  .card::after {
    content: "";
    position: absolute;
    left: 0;
    right: 0;
    bottom: 0;
    height: 8px;
    background: linear-gradient(90deg, var(--violet), var(--rose), var(--accent), var(--sun), var(--leaf), var(--teal));
  }
  .card--back { left: 491px; top: 207px; }
  .card--front { left: 198px; top: 566px; }

  .services {
    position: absolute;
    left: 406px;
    top: 26px;
    margin: 0;
    padding: 0;
    list-style: none;
    font-family: "Roboto", sans-serif;
    font-size: 21px;
    line-height: 26.4px;
    color: var(--ink-soft);
  }
  .contact {
    position: absolute;
    left: 22px;
    top: 166px;
    margin: 0;
    font-family: "Roboto", sans-serif;
    font-style: normal;
    font-size: 21px;
    line-height: 26.4px;
    color: var(--ink);
  }
  .contact span { display: block; }

  .brand-mark {
    position: absolute;
    left: 218px;
    top: 36px;
    width: 114px;
    height: 114px;
  }
  .brand-name {
    position: absolute;
    left: 0;
    right: 0;
    top: 166px;
    margin: 0;
    text-align: center;
    font-family: "Montserrat", sans-serif;
    font-weight: 500;
    font-size: 36px;
    line-height: 44px;
    letter-spacing: -1.4px;
    color: var(--ink-soft);
  }
  .tagline {
    position: absolute;
    left: 0;
    right: 0;
    top: 218px;
    margin: 0;
    text-align: center;
    font-family: "Roboto", sans-serif;
    font-size: 18px;
    line-height: 22px;
    color: var(--rose);
  }
  .brand-url {
    position: absolute;
    left: 0;
    right: 0;
    top: 266px;
    margin: 0;
    text-align: center;
    font-family: "Roboto", sans-serif;
    font-size: 18px;
    line-height: 22px;
    color: var(--ink);
  }
</style>
</head>
<body>
  <main class="canvas">
    <section class="card card--back">
      <ul class="services">
        <li>Seminar</li>
        <li>Workshop</li>
        <li>Coaching</li>
        <li>Podcast</li>
      </ul>
      <address class="contact">
        <span class="contact__name">Darren Whitlow</span>
        <span class="contact__role">Health &amp; Wellbeing Life Coach</span>
        <span class="contact__phone">0491 372 615</span>
        <span class="contact__email">darren@brightcoreliving.example</span>
        <span class="contact__web">brightcoreliving.example</span>
      </address>
    </section>

    <section class="card card--front">
      <svg class="brand-mark" viewBox="0 0 114 114" aria-hidden="true">
        <circle cx="57" cy="57" r="57" fill="var(--accent)"/>
      </svg>
      <h1 class="brand-name">Bright Core Living</h1>
      <p class="tagline">The journey home starts with you</p>
      <p class="brand-url">www.brightcoreliving.example</p>
    </section>
  </main>
</body>
</html>
```